Letterhead for a German Distribution/Manufacturing Company

We need a professional Letterhead in a unique Design.
not to playful.
The Letterhead has to show show that we are a international company with headquater in Germany.
all details like adress, Vat Tax Number, Bank Accout, Eori, email, Company number has to be on the Letterhead.
for example use: VAT TAX DE5470318 Bank Account: Kestrel Bank IBAN DE412058731ß204683 Swift: MORV0417352 EORI 3150428697 Company Number: HRB 51806 Adress: VOLMINTA UG Ahornweg 7 Postal Code 06384 City Kaltmoorstadt Country: Germany Email: info@volminta-example.com
the design can be colored but doesnt have to be
Industry/Entity Type
Manufacturing and international distribution
Requirements
Must have
- show that we are a international company with headquater in Germany. our company infos and logo

```html
<!DOCTYPE html>
<html lang="en">
<head>
<meta charset="utf-8">
<title>Volminta Letterhead</title>
<link rel="stylesheet" href="https://fonts.googleapis.com/css2?family=Open+Sans:wght@400&family=Roboto:wght@400&display=swap">
<style>
  :root {
    --backdrop: #e2e2e2;
    --paper: #f8f8f8;
    --ink-strong: #454545;
    --ink-body: #5e5e5e;
    --signature-tone: #dfe1e6;
  }
  * { margin: 0; padding: 0; box-sizing: border-box; }
  html, body {
    width: 1153px; height: 1200px; overflow: hidden;
    background: var(--backdrop);
  }
  .letterhead {
    position: absolute; left: 160px; top: 20px;
    width: 832px; height: 1160px;
    background: var(--paper);
    font-family: "Roboto", Arial, sans-serif;
    color: var(--ink-strong);
  }
  .brand {
    position: absolute; left: 82px; top: 54px; height: 78px;
    display: flex; align-items: center; gap: 12px;
  }
  .brand-dot {
    width: 52px; height: 52px; border-radius: 50%;
    background: var(--ink-strong);
  }
  .brand-name {
    font-size: 40px; font-weight: 400; letter-spacing: 0.3px;
    color: var(--ink-strong);
  }
  .company-address {
    position: absolute; left: 416px; top: 66px;
    font-size: 13.5px; line-height: 17.8px; font-style: normal;
    white-space: nowrap;
  }
  .contact-list {
    position: absolute; left: 590px; top: 66px;
    list-style: none; font-size: 13.5px; line-height: 17.8px;
    white-space: nowrap;
  }
  .contact-list li { display: flex; align-items: center; gap: 7px; }
  .contact-list svg { width: 12px; height: 12px; fill: var(--ink-strong); flex: none; }
  .letter-body {
    position: absolute; left: 82px; top: 285px; width: 667px;
    font-family: "Open Sans", Arial, sans-serif;
    font-size: 14.7px; line-height: 21.9px; color: var(--ink-body);
  }
  .letter-body p { margin-bottom: 21.9px; text-align: justify; }
  .letter-body .salutation, .letter-body .closing { text-align: left; }
  .signature {
    position: absolute; left: 83px; top: 865px;
    width: 94px; height: 86px; border-radius: 6px;
    background: var(--signature-tone);
  }
  .legal-footer {
    position: absolute; left: 82px; top: 1058px;
    font-size: 13.8px; line-height: 19.4px;
    white-space: nowrap;
  }
  .legal-footer .divider { font-weight: 700; padding: 0 3px; }
  .footer-mark {
    position: absolute; left: 671px; top: 1021px;
    width: 78px; height: 78px; border-radius: 50%;
    background: var(--ink-strong);
  }
</style>
</head>
<body>
  <article class="letterhead">
    <header>
      <div class="brand">
        <span class="brand-dot"></span>
        <span class="brand-name">VOLMINTA</span>
      </div>
      <address class="company-address">
        VOLMINTA UG<br>
        Ahornweg 7 06384<br>
        City Kaltmoorstadt Germany
      </address>
      <ul class="contact-list">
        <li>
          <svg viewBox="0 0 12 12" aria-hidden="true"><path d="M1 4c0-2 2-3 5-3s5 1 5 3v1H8.5V3.8h-5V5H1zM3 6h6l1 5H2z"/></svg>
          555.014.2290
        </li>
        <li>
          <svg viewBox="0 0 12 12" aria-hidden="true"><path d="M0 2.5h12v1L6 7 0 3.5zM0 5l6 3.5L12 5v4.5H0z"/></svg>
          info@volminta-example.com
        </li>
        <li>
          <svg viewBox="0 0 12 12" aria-hidden="true"><circle cx="6" cy="6" r="5.5"/></svg>
          www.volminta-example.com
        </li>
      </ul>
    </header>

    <section class="letter-body">
      <p class="salutation">Dear customer,</p>
      <p>Lorem ipsum dolor sit amet, consectetur adipisicing elit, sed do eiusmod tempor incididunt ut labore et dolore magna aliqua. Ut enim ad minim veniam, quis nostrud exercitation ullamco laboris nisi ut aliquip ex ea commodo consequat. Duis aute irure dolor in reprehenderit in voluptate velit esse cillum dolore eu fugiat nulla pariatur. Excepteur sint occaecat cupidatat non proident, sunt in culpa qui officia deserunt mollit anim id est laborum.</p>
      <p>Lorem ipsum dolor sit amet, consectetur adipisicing elit, sed do eiusmod tempor incididunt ut labore et dolore magna aliqua. Ut enim ad minim veniam, quis nostrud exercitation ullamco laboris nisi ut aliquip ex ea commodo consequat. Duis aute irure dolor in reprehenderit in voluptate velit esse cillum dolore eu fugiat nulla pariatur. Excepteur sint occaecat cupidatat non proident, sunt in culpa qui officia deserunt mollit anim id est laborum.</p>
      <p>Lorem ipsum dolor sit amet, consectetur adipisicing elit, sed do eiusmod tempor incididunt ut labore et dolore magna aliqua. Ut enim ad minim veniam, quis nostrud exercitation ullamco laboris nisi ut aliquip ex ea commodo consequat. Duis aute irure dolor in reprehenderit in voluptate velit esse cillum dolore eu fugiat nulla pariatur. Excepteur sint occaecat cupidatat non proident, sunt in culpa qui officia deserunt mollit anim id est laborum.</p>
      <p>Lorem ipsum dolor sit amet, consectetur adipisicing elit, sed do eiusmod tempor incididunt ut labore et dolore magna aliqua. Ut enim ad minim veniam, quis nostrud exercitation ullamco laboris nisi ut aliquip ex ea commodo consequat. Duis aute irure dolor in reprehenderit.</p>
      <p class="closing">Yours Sincerely,</p>
    </section>

    <div class="signature" role="img" aria-label="Handwritten signature of the sender"></div>

    <footer class="legal-footer">
      VAT TAX DE5470318<br>
      Bank Account: Kestrel Bank IBAN DE412058731ß204683<br>
      Swift: MORV0417352 EORI 3150428697<span class="divider">|</span>Company Number: HRB 51806
    </footer>
    <div class="footer-mark" aria-hidden="true"></div>
  </article>
</body>
</html>
```